Corporate Dinner Invite at Corvessa for BRQ

BRQ is hosting a corporate dinner at the VEP Summit and we need an email attachment invite for the event. Please use some images from this site for inspiration: https://www.corvessadining.example/ivyparlor/

Invite Title:
Join us for dinner!

Event Details:
Tuesday, October 24th 2023 at 6:30pm
Corvessa Dining, Ivy Parlor
347 W Marlow Ave, Chicago, IL 60622

Target Market(s)

Corporate Audience

Font styles to use
Script

Colors
0054AA
0677BA
7BADD7
CADEEF
E8F1F8

Requirements
Must have
• BRQ logo, event date / time, event location details, photo(s) from Ivy Parlor

```html
<!DOCTYPE html>
<html lang="en">
<head>
<meta charset="utf-8">
<title>BRQ Dinner Invitation – VEP Summit</title>
<link rel="stylesheet" href="https://fonts.googleapis.com/css2?family=Alex+Brush&family=Great+Vibes&family=Montserrat:wght@700&family=Noto+Serif:ital@0;1&display=swap">
<style>
  :root {
    --paper: #ffffff;
    --brand-navy: #1b2a8f;
    --accent-cyan: #19d3f0;
    --accent-orange: #f26b10;
    --script-blue: #1414e0;
    --detail-navy: #1d1d9c;
    --stripe-deep: #8fa0e0;
    --stripe-light: #dff4fb;
    --photo-dark: #1c120b;
    --photo-warm: #6b4523;
    --photo-glow: #b98342;
  }
  * { margin: 0; padding: 0; box-sizing: border-box; }
  html, body { width: 900px; height: 1200px; overflow: hidden; background: var(--paper); }
  .invite { position: relative; width: 900px; height: 1200px; background: var(--paper); overflow: hidden; }

  .corner-stripes { position: absolute; width: 230px; height: 230px; }
  .corner-stripes.top-left { left: 0; top: 0; }
  .corner-stripes.top-right { right: 0; top: 0; transform: scaleX(-1); }
  .corner-stripes.bottom-left { left: 0; bottom: 0; transform: scaleY(-1); }
  .corner-stripes.bottom-right { right: 0; bottom: 0; transform: scale(-1, -1); }

  .brand-mark {
    position: absolute; left: 0; right: 0; top: 128px;
    display: flex; justify-content: center; align-items: center; gap: 14px;
  }
  .brand-mark .brand-square { width: 26px; height: 26px; background: var(--brand-navy); }
  .brand-mark .brand-name {
    font-family: "Montserrat", sans-serif; font-weight: 700; font-size: 58px;
    color: var(--brand-navy); letter-spacing: 2px; line-height: 1;
  }

  .invite-title { position: absolute; left: 0; top: 270px; width: 900px; height: 180px; font-weight: 400; }
  .invite-title .lead {
    position: absolute; left: 396px; top: 12px;
    font-family: "Noto Serif", serif; font-weight: 400; font-size: 48px;
    color: var(--accent-cyan); line-height: 1; white-space: nowrap;
  }
  .invite-title .headline {
    position: absolute; left: 186px; top: 26px;
    font-family: "Alex Brush", cursive; font-weight: 400; font-size: 172px;
    color: var(--accent-orange); line-height: 1; white-space: nowrap;
  }

  .photo {
    position: absolute; border: 6px solid var(--paper);
    box-shadow: 3px 4px 10px rgba(0,0,0,0.28);
  }
  .photo.cocktails {
    left: 80px; top: 500px; width: 278px; height: 190px; transform: rotate(14deg);
    background: radial-gradient(circle at 50% 70%, var(--photo-glow), var(--photo-warm) 40%, var(--photo-dark) 85%);
  }
  .photo.dining-room {
    left: 318px; top: 520px; width: 278px; height: 190px; transform: rotate(14deg);
    background: radial-gradient(circle at 45% 50%, #8a6336, var(--photo-warm) 35%, var(--photo-dark) 90%);
  }
  .photo.bar-lounge {
    left: 515px; top: 540px; width: 305px; height: 190px; transform: rotate(13deg);
    background: radial-gradient(circle at 65% 45%, #c59a58, var(--photo-warm) 38%, var(--photo-dark) 88%);
  }

  .invite-line {
    position: absolute; left: 0; width: 900px; text-align: center; line-height: 1;
  }
  .invite-line.dine {
    top: 764px; padding-left: 12px;
    font-family: "Great Vibes", cursive; font-size: 50px; color: var(--script-blue);
    -webkit-text-stroke: 0.6px var(--script-blue);
  }
  .invite-line.venue-event {
    top: 815px; font-family: "Montserrat", sans-serif; font-weight: 700;
    font-size: 41px; color: var(--accent-cyan);
  }

  .details { position: absolute; left: 231px; top: 873px; width: 426px; height: 142px; }
  .details .rule { position: absolute; left: 0; width: 100%; border-top: 1.5px dotted var(--accent-cyan); }
  .details .rule.top { top: 0; }
  .details .rule.bottom { bottom: 0; }
  .details .divider { position: absolute; left: 197px; top: 7px; height: 126px; border-left: 1.5px solid var(--accent-cyan); }
  .details .divider-dot {
    position: absolute; left: 193px; top: 66px; width: 9px; height: 9px;
    border-radius: 50%; background: var(--accent-cyan);
  }
  .details .column {
    position: absolute; top: 10px;
    font-family: "Noto Serif", serif; font-style: italic; font-size: 24px; line-height: 31px;
    color: var(--detail-navy); white-space: nowrap;
  }
  .details .when { left: 24px; }
  .details .where { left: 218px; }
  .details .where .venue-name { color: var(--accent-cyan); }

  .sign-off {
    position: absolute; left: 0; top: 1032px; width: 900px; text-align: center; padding-left: 16px;
    font-family: "Great Vibes", cursive; font-size: 88px; line-height: 1.1;
    color: var(--script-blue); -webkit-text-stroke: 1px var(--script-blue);
  }
</style>
</head>
<body>
<main class="invite">
  <svg class="corner-stripes top-left" viewBox="0 0 230 230" role="img" aria-label="Decorative pastel blue corner stripes">
    <defs>
      <linearGradient id="cornerFade" x1="0" y1="0" x2="1" y2="1">
        <stop offset="0" stop-color="#8fa0e0"/>
        <stop offset="0.6" stop-color="#dff4fb"/>
        <stop offset="1" stop-color="#ffffff" stop-opacity="0"/>
      </linearGradient>
    </defs>
    <polygon points="0,0 230,0 0,230" fill="url(#cornerFade)"/>
  </svg>
  <svg class="corner-stripes top-right" viewBox="0 0 230 230" role="img" aria-label="Decorative pastel blue corner stripes">
    <polygon points="0,0 230,0 0,230" fill="url(#cornerFade)"/>
  </svg>
  <svg class="corner-stripes bottom-left" viewBox="0 0 230 230" role="img" aria-label="Decorative pastel blue corner stripes">
    <polygon points="0,0 230,0 0,230" fill="url(#cornerFade)"/>
  </svg>
  <svg class="corner-stripes bottom-right" viewBox="0 0 230 230" role="img" aria-label="Decorative pastel blue corner stripes">
    <polygon points="0,0 230,0 0,230" fill="url(#cornerFade)"/>
  </svg>

  <header class="brand-mark">
    <span class="brand-square"></span>
    <span class="brand-name">BRQ</span>
  </header>

  <h1 class="invite-title">
    <span class="lead">Join us for</span>
    <span class="headline">Dinner!</span>
  </h1>

  <div class="photo cocktails" role="img" aria-label="Photo of cocktails lined up on a bar counter"></div>
  <div class="photo dining-room" role="img" aria-label="Photo of the candlelit Ivy Parlor dining room with arched mirrors"></div>
  <div class="photo bar-lounge" role="img" aria-label="Photo of the warmly lit Ivy Parlor bar and lounge seating"></div>

  <p class="invite-line dine">Come and Dine with us</p>
  <p class="invite-line venue-event">@ VEP Summit</p>

  <section class="details">
    <span class="rule top"></span>
    <span class="divider"></span>
    <span class="divider-dot"></span>
    <p class="column when">Tuesday,<br>October 24th,<br>2023<br>@ 6:30pm</p>
    <p class="column where"><span class="venue-name">Corvessa Dining,</span><br>Ivy Parlor<br>347 W Marlow Ave,<br>Chicago, IL 60622</p>
    <span class="rule bottom"></span>
  </section>

  <p class="sign-off">See You There!</p>
</main>
</body>
</html>
```